Agriculture Business Card

I want to use my existing logo and use my tagline of "Don't Guess...Soil Test" on the card. Looking for a double sided card that will really get peoples attention.
Contact Info:
Marlow Field Crop Edge
Calvin Brusk
2917 K Lane
Larkin, NE 68593
402-555-0193
calvin.r.brusk@fieldmailbox.net

```html
<!DOCTYPE html>
<html lang="en">
<head>
<meta charset="utf-8">
<title>Marlow Field Crop Edge – Business Card</title>
<link href="https://fonts.googleapis.com/css2?family=Fira+Sans+Condensed:wght@500;600&family=Yanone+Kaffeesatz:wght@500&display=swap" rel="stylesheet">
<style>
  :root {
    --bg: #c3c4c6;
    --card: #ffffff;
    --gold: #fbb516;
    --brown: #8b4a2f;
    --green: #3fae49;
    --orange: #f6a81c;
  }
  * { margin: 0; padding: 0; box-sizing: border-box; }
  html, body { width: 900px; height: 1200px; overflow: hidden; background: var(--bg); }
  .canvas { position: relative; width: 900px; height: 1200px; }
  .card {
    position: absolute; left: 123px; width: 657px; height: 375px;
    background: var(--card); border-radius: 14px; overflow: hidden;
  }
  .card--front { top: 190px; }
  .card--back { top: 622px; }

  .brand {
    font-family: "Yanone Kaffeesatz", sans-serif; font-weight: 500;
    color: var(--brown); text-align: center; line-height: 0.98;
  }
  .brand-dot { display: block; border-radius: 50%; background: var(--gold); margin: 0 auto; }

  .front-brand { position: absolute; left: 0; right: 0; top: 88px; font-size: 29px; }
  .front-brand .brand-dot { width: 110px; height: 110px; margin-bottom: 22px; }

  .back-brand { position: absolute; left: 38px; width: 157px; top: 40px; font-size: 24px; }
  .back-brand .brand-dot { width: 92px; height: 92px; margin-bottom: 26px; }

  .large-brand { position: absolute; left: 373px; width: 251px; top: 150px; font-size: 34px; }
  .large-brand .brand-dot { width: 120px; height: 120px; margin-bottom: 14px; }

  .info { font-family: "Fira Sans Condensed", sans-serif; font-weight: 600; color: var(--brown); letter-spacing: 0.6px; }
  .address {
    position: absolute; left: 53px; top: 210px; width: 140px;
    border-top: 1px solid var(--gold); border-bottom: 1px solid var(--gold);
    padding: 7px 0 5px; font-size: 14.5px; line-height: 26px;
  }
  .contact { position: absolute; left: 53px; top: 285px; font-size: 14.5px; line-height: 25px; list-style: none; }
  .contact li { display: flex; align-items: center; gap: 7px; }
  .contact svg { width: 13px; height: 13px; fill: var(--gold); }

  .person { position: absolute; right: 35px; top: 30px; text-align: right; font-family: "Fira Sans Condensed", sans-serif; }
  .person-name { font-size: 27px; font-weight: 600; color: var(--gold); letter-spacing: 1px; line-height: 1.1; }
  .person-role { font-size: 15px; font-weight: 500; color: var(--brown); letter-spacing: 0.5px; }

  .swoosh { position: absolute; left: 0; top: 0; width: 657px; height: 375px; }
  .tagline {
    position: absolute; left: 415px; top: 347px;
    font-family: "Fira Sans Condensed", sans-serif; font-weight: 600; font-size: 14px;
    color: #fff; letter-spacing: 1.2px;
  }
</style>
</head>
<body>
<div class="canvas">
  <section class="card card--front">
    <div class="brand front-brand">
      <span class="brand-dot"></span>
      Marlow Field Crop<br>Edge
    </div>
  </section>

  <section class="card card--back">
    <svg class="swoosh" viewBox="0 0 657 375" aria-hidden="true">
      <path d="M59 375 Q300 338 657 334 L657 339 Q320 343 88 375 Z" fill="var(--orange)"/>
      <path d="M100 375 Q330 342 657 338 L657 375 Z" fill="var(--green)"/>
    </svg>

    <div class="brand back-brand">
      <span class="brand-dot"></span>
      Marlow Field Crop<br>Edge
    </div>

    <div class="info address">2917 K Lane<br>Larkin, NE 68593</div>
    <ul class="info contact">
      <li><svg viewBox="0 0 24 24"><path d="M6.6 10.8a15.1 15.1 0 0 0 6.6 6.6l2.2-2.2c.3-.3.7-.4 1-.2 1.1.4 2.3.6 3.6.6.6 0 1 .4 1 1V20c0 .6-.4 1-1 1C10.6 21 3 13.4 3 4c0-.6.4-1 1-1h3.5c.6 0 1 .4 1 1 0 1.3.2 2.5.6 3.6.1.3 0 .7-.2 1z"/></svg>402-555-0193</li>
      <li><svg viewBox="0 0 24 24"><path d="M2 5h20v14H2z M2 5l10 8 10-8" fill="var(--gold)" stroke="#fff" stroke-width="1.5"/></svg>calvin.r.brusk@fieldmailbox.net</li>
    </ul>

    <div class="person">
      <div class="person-name">CALVIN BRUSK</div>
      <div class="person-role">Owner</div>
    </div>

    <div class="brand large-brand">
      <span class="brand-dot"></span>
      Marlow Field Crop Edge
    </div>

    <div class="tagline">DON'T GUESS...SOIL TEST</div>
  </section>
</div>
</body>
</html>
```